Ward Compass Business Card Design*

We need a business card design for our company Ward Compass. Our company is specialized in providing online consulting services regarding medical institutions, hospitals and doctors. We work with patients worldwide looking to choose between healthcare providers. We have a website you may use as a reference, where we list doctors and clinics worldwide. So we target Medical providers as well as patients worldwide.
Target Market(s)
Medical Providers and patients around the world
Industry/Entity Type
Medical
Contact Information for Business Card
Salwa Kettani
CEO
+90 612 348 2175
info@wardcompass.example
www.wardcompass.example
14 Annakhil 7 H.R.B. Rabat, Morocco
Requirements
Must have
- Company logo/name on one full side, personal info and smaller logo and company name on the other side.
Nice to have
- Smart and elegant design

```html
<!DOCTYPE html>
<html lang="en">
<head>
<meta charset="utf-8">
<title>Ward Compass — Business Card</title>
<link rel="stylesheet" href="https://fonts.googleapis.com/css2?family=Montserrat:wght@400;600;700&family=Roboto:wght@400;500&display=swap">
<style>
  :root {
    --navy: #163a66;
    --grey: #7b7b7b;
    --ink-soft: #8a8a8a;
    --paper: #ffffff;
    --backdrop: #e6e7e9;
    --ghost: #f3f4f6;
  }
  * { box-sizing: border-box; margin: 0; padding: 0; }
  html, body { width: 1200px; height: 900px; overflow: hidden; }
  body {
    background: var(--backdrop);
    font-family: "Roboto", Arial, sans-serif;
    position: relative;
  }
  .card {
    position: absolute;
    left: 260px;
    width: 680px;
    height: 388px;
    box-shadow: 0 6px 18px rgba(0,0,0,0.12);
    overflow: hidden;
  }
  .card--front { top: 45px; background: var(--navy); }
  .card--back { top: 467px; background: var(--paper); }

  .wordmark {
    display: flex;
    align-items: center;
    gap: 14px;
    font-family: "Montserrat", Arial, sans-serif;
    font-weight: 600;
    text-transform: uppercase;
    letter-spacing: 0.06em;
  }
  .wordmark__dot { border-radius: 50%; flex: none; }

  .card--front .wordmark {
    position: absolute;
    left: 50%; top: 50%;
    transform: translate(-50%, -50%);
    color: var(--paper);
    font-size: 34px;
  }
  .card--front .wordmark__dot { width: 44px; height: 44px; background: var(--grey); }

  .card--back .ghost-disc {
    position: absolute;
    right: 58px; top: -60px;
    width: 260px; height: 260px;
    border-radius: 50%;
    background: var(--ghost);
  }
  .card--back .wordmark {
    position: absolute;
    left: 48px; top: 108px;
    color: var(--navy);
    font-size: 24px;
    gap: 12px;
  }
  .card--back .wordmark__dot { width: 34px; height: 34px; background: var(--navy); }

  .divider {
    position: absolute;
    left: 190px; right: 52px; top: 246px;
    height: 1.5px;
    background: var(--navy);
  }
  .person { position: absolute; left: 48px; top: 206px; }
  .person__name {
    font-family: "Roboto", Arial, sans-serif;
    font-weight: 500;
    font-size: 24px;
    color: var(--navy);
    text-transform: uppercase;
    letter-spacing: 0.01em;
  }
  .person__role {
    font-size: 20px;
    color: var(--grey);
    font-weight: 500;
    margin-top: 2px;
  }
  .contacts {
    position: absolute;
    left: 48px; top: 288px;
    list-style: none;
    font-size: 15px;
    color: var(--ink-soft);
  }
  .contacts li { display: flex; align-items: center; gap: 12px; height: 26px; }
  .contacts svg { width: 14px; height: 14px; fill: var(--navy); flex: none; }

  .address {
    position: absolute;
    right: 52px; top: 262px;
    text-align: right;
    font-size: 15px;
    line-height: 1.35;
    color: var(--ink-soft);
  }
</style>
</head>
<body>
  <section class="card card--front" aria-label="Card front">
    <div class="wordmark">
      <span class="wordmark__dot" aria-hidden="true"></span>
      <span class="wordmark__name">Ward Compass</span>
    </div>
  </section>

  <section class="card card--back" aria-label="Card back">
    <span class="ghost-disc" aria-hidden="true"></span>
    <div class="wordmark">
      <span class="wordmark__dot" aria-hidden="true"></span>
      <span class="wordmark__name">Ward Compass</span>
    </div>

    <div class="person">
      <p class="person__name">Salwa Kettani</p>
      <p class="person__role">CEO</p>
    </div>
    <span class="divider" aria-hidden="true"></span>

    <ul class="contacts">
      <li>
        <svg viewBox="0 0 24 24" aria-hidden="true"><path d="M6.6 10.8a15.1 15.1 0 0 0 6.6 6.6l2.2-2.2a1 1 0 0 1 1-.25 11.4 11.4 0 0 0 3.6.57 1 1 0 0 1 1 1V20a1 1 0 0 1-1 1A17 17 0 0 1 3 4a1 1 0 0 1 1-1h3.5a1 1 0 0 1 1 1c0 1.25.2 2.45.57 3.57a1 1 0 0 1-.25 1z"/></svg>
        <span>+90 612 348 2175</span>
      </li>
      <li>
        <svg viewBox="0 0 24 24" aria-hidden="true"><path d="M2 5h20v14H2zm2 2v.5l8 5 8-5V7zm0 2.9V17h16V9.9l-8 5z"/></svg>
        <span>info@wardcompass.example</span>
      </li>
      <li>
        <svg viewBox="0 0 24 24" aria-hidden="true"><path d="M12 2a10 10 0 1 0 0 20 10 10 0 0 0 0-20zm-1 17.9A8 8 0 0 1 4.1 10l4.9 5v1a2 2 0 0 0 2 2zm6.9-2.5A2 2 0 0 0 16 16h-1v-3a1 1 0 0 0-1-1H8v-2h2a1 1 0 0 0 1-1V7h2a2 2 0 0 0 2-2v-.4a8 8 0 0 1 2.9 12.8z"/></svg>
        <span>www.wardcompass.example</span>
      </li>
    </ul>

    <address class="address" style="font-style: normal;">
      14 Annakhil 7 H.R.B.<br>
      Rabat, Morocco
    </address>
  </section>
</body>
</html>
```